BuildLinkHub.com Full Stationery Design

Business Card will have all info on it. Letterhead will not have name, title or mobile number. Keep general feeling very clean, using colors from the logo as accents.
Name:Dale Marchetti
Title:President
Phone: 1-800-555-0142
Cell: 306-555-0187
email: dale@buildlinkhub.example
website: www.buildlinkhub.example
Address:
PO Box 947
Larkview, SK
S0J2T0

Target Market(s)

Construction Business owners

Industry/Entity Type

Business

Contact Information for Business Card

Name:Dale Marchetti
Title:President
Phone: 1-800-555-0142
Cell: 306-555-0187
Address:
PO Box 947
Larkview, SK
S0J2T0

Font styles to use
Sans Serif

Requirements
Must have
• Clean look
Should not have
• Images or cartoon type characters or tools

```html
<!DOCTYPE html>
<html lang="en">
<head>
<meta charset="utf-8">
<title>BuildLinkHub.com Business Card</title>
<link href="https://fonts.googleapis.com/css2?family=Source+Sans+3:wght@400;600;700&display=swap" rel="stylesheet">
<style>
  :root {
    --backdrop: #ecebe8;
    --slate-top: #4a5a6d;
    --slate-bottom: #6b8093;
    --accent-orange: #f58220;
    --accent-red: #e8262e;
    --ink: #46525f;
    --muted: #4a4a4a;
    --paper: #ffffff;
    --line-light: #ffffff;
  }
  * { margin: 0; padding: 0; box-sizing: border-box; }
  html, body {
    width: 1200px; height: 987px; overflow: hidden;
    background: var(--backdrop);
    font-family: "Source Sans 3", "Myriad Pro", sans-serif;
  }
  .canvas { position: relative; width: 1200px; height: 987px; }
  .card {
    position: absolute; left: 293px; width: 615px; height: 351px;
    box-shadow: 0 2px 6px rgba(0,0,0,0.25);
    overflow: hidden;
  }
  .card--front {
    top: 130px;
    background: linear-gradient(180deg, var(--slate-top), var(--slate-bottom));
    color: var(--line-light);
  }
  .card--back { top: 505px; background: var(--paper); }

  .corner-accents { position: absolute; left: 0; top: 0; width: 615px; height: 351px; }
  .holder { position: absolute; left: 37px; top: 32px; }
  .holder__name { font-weight: 700; font-size: 22px; color: var(--accent-orange); line-height: 1.1; }
  .holder__title { font-weight: 400; font-size: 17px; line-height: 1.3; }

  .address { position: absolute; left: 37px; top: 175px; font-size: 15px; line-height: 21px; font-style: normal; }
  .contacts { position: absolute; left: 37px; top: 226px; list-style: none; font-size: 15px; }
  .contacts li { display: flex; align-items: center; height: 23.5px; }
  .contacts svg { width: 15px; height: 15px; margin-right: 9px; fill: var(--accent-orange); flex: none; }

  .brand {
    position: absolute; left: 0; right: 0; top: 150px;
    display: flex; justify-content: center; align-items: center; gap: 14px;
  }
  .brand__mark { width: 22px; height: 22px; background: var(--accent-orange); }
  .brand__name { font-weight: 600; font-size: 40px; color: var(--ink); line-height: 1; }
  .back-web {
    position: absolute; left: 0; right: 0; top: 289px;
    text-align: center; font-size: 16px; color: var(--muted);
  }
</style>
</head>
<body>
<main class="canvas">
  <section class="card card--front">
    <svg class="corner-accents" viewBox="0 0 615 351" aria-hidden="true">
      <defs>
        <linearGradient id="accent-fade" x1="0" y1="0" x2="0" y2="1">
          <stop offset="0" stop-color="#f58220"/>
          <stop offset="1" stop-color="#e8262e"/>
        </linearGradient>
      </defs>
      <polygon points="462,0 615,0 615,87" fill="url(#accent-fade)"/>
      <polygon points="462,351 615,266 615,351" fill="url(#accent-fade)"/>
    </svg>
    <div class="holder">
      <p class="holder__name">Dale Marchetti</p>
      <p class="holder__title">President</p>
    </div>
    <address class="address">
      PO Box 947<br>Larkview, SK, S0J2T0
    </address>
    <ul class="contacts">
      <li>
        <svg viewBox="0 0 16 16"><path d="M3.5 1.5l2.5 0 1 3.5-1.8 1.2c.8 1.8 2.2 3.2 4 4l1.2-1.8 3.5 1v2.5c0 .8-.7 1.5-1.5 1.5C6.8 13.4 2.6 9.2 2 3c0-.8.7-1.5 1.5-1.5z"/></svg>
        1-800-555-0142
      </li>
      <li>
        <svg viewBox="0 0 16 16"><path d="M4.5 1h7c.6 0 1 .4 1 1v12c0 .6-.4 1-1 1h-7c-.6 0-1-.4-1-1V2c0-.6.4-1 1-1zm.8 2v9h5.4V3zM8 12.8a.8.8 0 100 1.6.8.8 0 000-1.6z"/></svg>
        306-555-0187
      </li>
      <li>
        <svg viewBox="0 0 16 16"><path d="M1 3.5h14L8 8.8z"/><path d="M1 4.8l7 5.3 7-5.3v7.7H1z"/></svg>
        dale@buildlinkhub.example
      </li>
      <li>
        <svg viewBox="0 0 16 16"><circle cx="8" cy="8" r="7"/><path d="M1.5 8h13M8 1c2 2 2 12 0 14M8 1c-2 2-2 12 0 14" stroke="#5e7386" stroke-width="1" fill="none"/></svg>
        www.buildlinkhub.example
      </li>
    </ul>
  </section>

  <section class="card card--back">
    <div class="brand">
      <span class="brand__mark"></span>
      <span class="brand__name">BuildLinkHub.com</span>
    </div>
    <p class="back-web">www.buildlinkhub.example</p>
  </section>
</main>
</body>
</html>
```